Fenwick Grading LTD - website for irrigation & Landscape Lighting & Buried service wire

Looking for a website to help promote my business with Irrigation (installation, service, etc) and buried service wire/drainage solutions.

Commercial/Residential

Landscape lighting.

I’ll get photos in the trucks and trailers to upload as well maybe the machine as well.

Target Market(s)

Homeowners who want green grass and beautiful gardens. Beautiful landscape lighting

Industry/Entity Type

Irrigation systems and landscape lighting and buried service wire to homes and offering Drainage soltions.

Coding

Coded - Design and coding required

Number of Pages Required

4 page

Colors
F0912C
F2A743
F7CA91
FBE8D2
FDF5EE

Requirements
Must have
• was hoping to link up my email on fenwickgrading@mailbox-example.net with the website if possible.
Nice to have
• Page for Irrigation, page for landscape lighting, page buried service wire & drainage soltions.

```html
<!DOCTYPE html>
<html lang="en">
<head>
<meta charset="utf-8">
<title>Fenwick Grading LTD – Irrigation, Landscape Lighting &amp; Trenching</title>
<link href="https://fonts.googleapis.com/css2?family=Montserrat:wght@400;500;600;700&family=Roboto+Condensed:wght@700&display=swap" rel="stylesheet">
<style>
  :root {
    --orange: #F0912C;
    --orange-light: #F2A743;
    --peach: #F7CA91;
    --cream: #FBE8D2;
    --ivory: #FDF5EE;
    --ink: #111111;
    --text: #1c1c1c;
    --muted: #555555;
    --white: #ffffff;
    --black: #000000;
  }
  * { margin: 0; padding: 0; box-sizing: border-box; }
  html, body { width: 1200px; height: 3200px; overflow: hidden; }
  body {
    position: relative;
    background: var(--white);
    font-family: "Montserrat", sans-serif;
    color: var(--text);
  }
  .abs { position: absolute; }

  /* Buttons */
  .btn {
    position: absolute;
    display: inline-flex; align-items: center; justify-content: center;
    background: var(--orange);
    color: var(--white);
    font-family: "Montserrat", sans-serif;
    font-weight: 600; font-size: 12.5px; letter-spacing: 0.8px;
    text-transform: uppercase;
    border-radius: 22px;
    text-decoration: none;
  }

  /* Header */
  .hero-photo {
    position: absolute; left: 0; top: 0; width: 1200px; height: 620px;
    background:
      radial-gradient(ellipse at 80% 20%, #5a6b2a 0%, transparent 45%),
      radial-gradient(ellipse at 20% 55%, #4f7a22 0%, transparent 50%),
      linear-gradient(180deg, #2a3a1a 0%, #3d5420 45%, #4b6a24 70%, #3a4a22 100%);
  }
  .hero-shade {
    position: absolute; left: 0; top: 0; width: 1200px; height: 620px;
    background: linear-gradient(90deg, rgba(0,0,0,0.45) 0%, rgba(0,0,0,0.2) 55%, rgba(0,0,0,0.05) 100%);
  }
  .brand {
    position: absolute; display: flex; align-items: center; gap: 10px;
    color: var(--orange); font-family: "Montserrat", sans-serif; font-weight: 700;
    text-transform: uppercase; line-height: 1.05;
  }
  .brand-dot { border-radius: 50%; background: var(--orange); flex: none; }
  .site-brand { left: 140px; top: 28px; font-size: 21px; }
  .site-brand .brand-dot { width: 34px; height: 34px; }

  .main-nav { position: absolute; top: 33px; left: 386px; display: flex; gap: 45px; }
  .main-nav a { color: var(--white); font-size: 13.5px; text-decoration: none; font-weight: 500; }
  .main-nav a.active { color: var(--orange); border-bottom: 2px solid var(--orange); padding-bottom: 2px; }
  .header-cta { left: 940px; top: 25px; width: 118px; height: 34px; font-size: 12px; }

  .hero-title {
    position: absolute; left: 140px; top: 184px; width: 520px;
    font-family: "Roboto Condensed", sans-serif; font-weight: 700;
    font-size: 40px; line-height: 48px; color: var(--white);
  }
  .hero-text {
    position: absolute; left: 140px; top: 342px; width: 480px;
    font-size: 13px; line-height: 22.5px; color: var(--white); font-weight: 500;
  }
  .hero-cta { left: 140px; top: 431px; width: 234px; height: 39px; }
  .hero-edge { position: absolute; left: 0; top: 520px; }

  /* Section heading */
  .section-title {
    position: absolute; left: 0; width: 1200px; text-align: center;
    font-family: "Roboto Condensed", sans-serif; font-weight: 700;
    font-size: 37px; color: var(--ink);
  }
  .accent { color: var(--orange); }

  /* Services */
  .service-media { position: absolute; width: 390px; height: 380px; }
  .service-title { position: absolute; font-size: 26.5px; font-weight: 600; color: var(--ink); }
  .service-lead {
    position: absolute; border-left: 2px solid var(--orange); padding-left: 11px;
    font-size: 13px; line-height: 22.5px; font-weight: 500; color: var(--ink); width: 390px;
  }
  .service-body { position: absolute; font-size: 13px; line-height: 22.5px; color: var(--muted); width: 422px; }
  .service-cta { width: 123px; height: 35px; font-size: 12px; }

  /* Testimonials */
  .testimonial-title {
    position: absolute; left: 0; width: 1200px; text-align: center;
    font-size: 26px; font-weight: 600; color: var(--ink);
  }
  .testimonial-sub { position: absolute; left: 0; width: 1200px; text-align: center; font-size: 13px; font-weight: 500; }
  .quote { position: absolute; left: 140px; top: 2420px; width: 480px; font-size: 13px; line-height: 22.5px; color: var(--text); }
  .quote-author { position: absolute; left: 140px; top: 2552px; font-size: 16px; font-weight: 600; color: var(--orange); }
  .slider-arrows { position: absolute; left: 140px; top: 2624px; display: flex; gap: 55px; }
  .portrait { position: absolute; border-radius: 50%; }
  .portrait-main {
    position: absolute; left: 712px; top: 2350px; width: 232px; height: 340px;
    border-radius: 116px;
    background: linear-gradient(180deg, #c9d3dc 0%, #9aa7b1 45%, #2a2e36 100%);
  }
  .portrait-ring {
    position: absolute; left: 716px; top: 2350px; width: 232px; height: 344px;
    border-radius: 116px; border: 2px solid var(--orange); border-left-color: transparent; border-top-color: transparent;
  }

  /* Footer */
  .footer-shape { position: absolute; left: 0; top: 2770px; }
  .footer-brand { left: 0; width: 1200px; top: 2880px; justify-content: center; font-size: 30px; }
  .footer-brand .brand-dot { width: 44px; height: 44px; }
  .footer-nav { position: absolute; top: 3013px; left: 0; width: 1200px; display: flex; justify-content: center; gap: 50px; }
  .footer-nav a { color: var(--white); text-decoration: none; font-size: 13.5px; font-weight: 500; }
  .footer-nav a.active { color: var(--orange); }
  .footer-nav a.contact { font-weight: 600; font-size: 12.5px; }
  .contact-item { position: absolute; top: 3078px; display: flex; align-items: center; gap: 12px; color: var(--white); font-size: 13px; line-height: 21px; }
  .contact-icon {
    width: 36px; height: 36px; border-radius: 50%; border: 1.5px solid var(--orange);
    display: flex; align-items: center; justify-content: center; flex: none;
  }
  .footer-rule { position: absolute; left: 140px; top: 3137px; width: 918px; height: 1px; background: #333; }
  .copyright { position: absolute; left: 140px; top: 3158px; color: var(--white); font-size: 13px; }
  .social { position: absolute; top: 3152px; left: 904px; display: flex; gap: 9px; }
  .social span { width: 33px; height: 33px; border-radius: 50%; border: 1.5px solid var(--orange); display: flex; align-items: center; justify-content: center; }
  .social span::after { content: ""; width: 7px; height: 7px; border-radius: 50%; background: var(--white); }
</style>
</head>
<body>

<!-- Header / hero -->
<header>
  <div class="hero-photo" role="img" aria-label="Evening garden with lit bollard lights, lawn and shrubs"></div>
  <div class="hero-shade"></div>

  <div class="brand site-brand"><span class="brand-dot"></span><span>Fenwick<br>Grading LTD</span></div>

  <nav class="main-nav">
    <a href="#" class="active">Home</a>
    <a href="#">Irrigation</a>
    <a href="#">Landscape Lighting</a>
    <a href="#">Fiber Optic Installation</a>
  </nav>
  <a class="btn header-cta" href="#">Contact Us</a>

  <h1 class="hero-title">Transform Your Outdoor Space With Our Expert Irrigation And Lighting Solutions</h1>
  <p class="hero-text">Get The Perfect Blend Of Form And Function With Our State-Of-The-Art Irrigation Systems And Landscape Lighting.Trust Our Experienced Team To Deliver Top-Notch Fiber Optic Installation For Your Home</p>
  <a class="btn hero-cta" href="#">Free No Obligation Quotes</a>

  <svg class="hero-edge" width="1200" height="100" viewBox="0 0 1200 100">
    <polygon points="0,26 600,92 1200,14 1200,100 0,100" fill="var(--orange)"/>
    <polygon points="0,30 600,100 1200,22 1200,100 0,100" fill="var(--white)"/>
  </svg>
</header>

<!-- Services -->
<main>
  <h2 class="section-title" style="top:700px;">One Stop Solution For <span class="accent">All Outdoor Home Improvements</span></h2>

  <!-- Irrigation -->
  <svg class="service-media" style="left:149px; top:814px;" viewBox="0 0 390 380" role="img" aria-label="Rotating lawn sprinkler spraying water over a field">
    <defs>
      <linearGradient id="g-irrigation" x1="0" y1="0" x2="0" y2="1">
        <stop offset="0" stop-color="#8ea6c9"/><stop offset="0.55" stop-color="#b8c2cc"/><stop offset="1" stop-color="#3f5a2e"/>
      </linearGradient>
    </defs>
    <path d="M180 6 C250 4 360 60 378 170 C390 260 300 330 170 362 C80 385 0 360 4 270 C8 180 70 10 180 6 Z" fill="none" stroke="var(--orange)" stroke-width="1.5"/>
    <path d="M170 6 C240 10 340 70 365 170 C380 250 290 320 165 350 C75 372 -2 345 5 265 C12 180 70 2 170 6 Z" fill="url(#g-irrigation)"/>
  </svg>
  <h3 class="service-title" style="left:638px; top:858px;">Irrigation <span class="accent">Systems</span></h3>
  <p class="service-lead" style="left:638px; top:914px;">Efficient and Effective Watering Solutions for Your Lawn and Garden</p>
  <p class="service-body" style="left:638px; top:974px;">Our irrigation systems are designed to provide your lawn and garden with the right amount of water, without wasting a single drop. With our expert installation and service, you can rest assured that your plants will receive the nourishment they need to thrive.</p>
  <a class="btn service-cta" href="#" style="left:638px; top:1111px;">Learn More</a>

  <!-- Landscape lighting -->
  <h3 class="service-title" style="left:140px; top:1335px;">Landscape <span class="accent">Lighting</span></h3>
  <p class="service-lead" style="left:140px; top:1391px;">Enhance Your Outdoor Space with Beautiful and Functional Lighting Solutions</p>
  <p class="service-body" style="left:140px; top:1451px;">Our landscape lighting solutions are designed to enhance the beauty and functionality of your outdoor space. From subtle pathway lighting to dramatic spotlights, we'll work with you to create a lighting plan that meets your needs and complements your landscape.</p>
  <a class="btn service-cta" href="#" style="left:140px; top:1588px;">Learn More</a>
  <svg class="service-media" style="left:664px; top:1291px;" viewBox="0 0 390 380" role="img" aria-label="Garden at dusk with bollard lights beside lawn and grasses">
    <defs>
      <linearGradient id="g-lighting" x1="0" y1="0" x2="0" y2="1">
        <stop offset="0" stop-color="#2f3d22"/><stop offset="0.5" stop-color="#5e7e2c"/><stop offset="1" stop-color="#4a3a22"/>
      </linearGradient>
    </defs>
    <path d="M180 6 C250 4 360 60 378 170 C390 260 300 330 170 362 C80 385 0 360 4 270 C8 180 70 10 180 6 Z" fill="none" stroke="var(--orange)" stroke-width="1.5"/>
    <path d="M170 6 C240 10 340 70 365 170 C380 250 290 320 165 350 C75 372 -2 345 5 265 C12 180 70 2 170 6 Z" fill="url(#g-lighting)"/>
  </svg>

  <!-- Trenching -->
  <svg class="service-media" style="left:149px; top:1768px;" viewBox="0 0 390 380" role="img" aria-label="Spade cutting into grassy soil">
    <defs>
      <linearGradient id="g-trenching" x1="0" y1="0" x2="1" y2="1">
        <stop offset="0" stop-color="#6f8a3a"/><stop offset="0.5" stop-color="#8a9a6a"/><stop offset="1" stop-color="#7a5a3e"/>
      </linearGradient>
    </defs>
    <path d="M180 6 C250 4 360 60 378 170 C390 260 300 330 170 362 C80 385 0 360 4 270 C8 180 70 10 180 6 Z" fill="none" stroke="var(--orange)" stroke-width="1.5"/>
    <path d="M170 6 C240 10 340 70 365 170 C380 250 290 320 165 350 C75 372 -2 345 5 265 C12 180 70 2 170 6 Z" fill="url(#g-trenching)"/>
  </svg>
  <h3 class="service-title" style="left:638px; top:1834px;">Generic <span class="accent">Trenching</span></h3>
  <p class="service-lead" style="left:638px; top:1891px;">Lorem Ipsum Dolor Sit Amet, Consectetuer Adipiscing</p>
  <p class="service-body" style="left:638px; top:1928px;">Duis autem vel eum iriure dolor in hendrerit in vulputate velit esse molestie consequat, vel illum dolore eu feugiat nulla facilisis atl m vero eros et accumsan et iust odio dignissim qui blandit praesent luptatum zzril delenit augue duis dolore te nulla facilisi.</p>
  <a class="btn service-cta" href="#" style="left:638px; top:2043px;">Learn More</a>

  <!-- Testimonials -->
  <h2 class="testimonial-title" style="top:2240px;">What Our <span class="accent">Customers</span> Say</h2>
  <p class="testimonial-sub" style="top:2290px;">Hear from Our Satisfied Clients</p>

  <blockquote class="quote">They maintain around 52 acres for us including several thousand sq ft or beds. Always answer thr phone and very prompt if we ever have an issue. Great guys all the way around! It is a long established fact that a reader will be distracted by the readable content of a page when looking at its layout.</blockquote>
  <p class="quote-author">Marcus Delaney</p>
  <div class="slider-arrows">
    <svg width="36" height="16" viewBox="0 0 36 16" aria-label="Previous"><path d="M35 8H2M9 1L2 8l7 7" fill="none" stroke="var(--ink)" stroke-width="1.5"/></svg>
    <svg width="36" height="16" viewBox="0 0 36 16" aria-label="Next"><path d="M1 8h33M27 1l7 7-7 7" fill="none" stroke="var(--ink)" stroke-width="1.5"/></svg>
  </div>

  <div class="portrait-ring"></div>
  <div class="portrait-main" role="img" aria-label="Portrait photo of the featured customer"></div>
  <div class="portrait" role="img" aria-label="Customer portrait" style="left:946px; top:2300px; width:111px; height:111px; background:linear-gradient(180deg,#6a5a55,#b0303a);"></div>
  <div class="portrait" role="img" aria-label="Customer portrait" style="left:592px; top:2571px; width:80px; height:80px; background:linear-gradient(180deg,#6aa0b0,#3a4a3a);"></div>
  <div class="portrait" role="img" aria-label="Customer portrait" style="left:966px; top:2581px; width:70px; height:70px; background:linear-gradient(180deg,#c8c8c4,#5a4a3a);"></div>
</main>

<!-- Footer -->
<footer>
  <svg class="footer-shape" width="1200" height="430" viewBox="0 0 1200 430">
    <polygon points="0,77 600,0 1200,77 1200,430 0,430" fill="var(--orange)"/>
    <polygon points="0,85 600,8 1200,85 1200,430 0,430" fill="var(--black)"/>
  </svg>

  <div class="brand footer-brand"><span class="brand-dot"></span><span>Fenwick<br>Grading LTD</span></div>

  <nav class="footer-nav">
    <a href="#" class="active">Home</a>
    <a href="#">Irrigation</a>
    <a href="#">Landscape Lighting</a>
    <a href="#">Fiber Optic Installation</a>
    <a href="#" class="contact">Contact Us</a>
  </nav>

  <div class="contact-item" style="left:207px;">
    <span class="contact-icon"><svg width="14" height="16" viewBox="0 0 14 16"><path d="M7 1a5 5 0 0 0-5 5c0 4 5 9 5 9s5-5 5-9a5 5 0 0 0-5-5z" fill="var(--white)"/><circle cx="7" cy="6" r="2" fill="var(--black)"/></svg></span>
    <span>123, Building Name, Street<br>City, State XY 123456</span>
  </div>
  <div class="contact-item" style="left:528px;">
    <span class="contact-icon"><svg width="14" height="14" viewBox="0 0 24 24"><path d="M6.6 10.8a15.1 15.1 0 0 0 6.6 6.6l2.2-2.2a1 1 0 0 1 1-.25 11.4 11.4 0 0 0 3.6.57 1 1 0 0 1 1 1V20a1 1 0 0 1-1 1A17 17 0 0 1 3 4a1 1 0 0 1 1-1h3.5a1 1 0 0 1 1 1c0 1.25.2 2.45.57 3.57a1 1 0 0 1-.25 1z" fill="var(--white)"/></svg></span>
    <span>Phone<br>123-456-7890</span>
  </div>
  <div class="contact-item" style="left:765px;">
    <span class="contact-icon"><svg width="14" height="11" viewBox="0 0 14 11"><rect x="0" y="0" width="14" height="11" rx="1.5" fill="var(--white)"/><path d="M1 1.5l6 4.5 6-4.5" fill="none" stroke="var(--black)" stroke-width="1.2"/></svg></span>
    <span>E-Mail<br>info@fenwickgrading-example.net</span>
  </div>

  <div class="footer-rule"></div>
  <p class="copyright">© 2024 Fenwick Grading Ltd . All Rights Reserved.</p>
  <div class="social" aria-label="Social media links">
    <span></span><span></span><span></span><span></span>
  </div>
</footer>

</body>
</html>
```